Wordpress 6 pages GLAM design for hair salon

Hi guys.
I need a glam & easy to navigate web design for my (women only) new hair salon.
I have a logo. You can see in attached files.
I like 3d backgrounds.
My favourite colours choice: any variety of pink(hot & very soft), white, black, grey.
I would like to see website very feminine, glamorous & kind of old Hollywood and Dorinda Calloway inspired.
Of course it should have plug ins, like social media, map, security etc.
My website now: http://velmoracoiffure.example

Designs what I like:
http://torvinellastudio.example
http://pelurabeautyloft.example
http://www.quillfernvisualworks.example/boutique-graphic-web-folio.html
Updates

Target Market(s)

WOMEN

Industry/Entity Type

Boutique

Requirements
Should not have
• any cartoon or other characters!

```html
<!DOCTYPE html>
<html lang="en">
<head>
<meta charset="utf-8">
<title>Velmora Coiffure</title>
<link rel="stylesheet" href="https://fonts.googleapis.com/css2?family=Ubuntu:wght@300;400;500&display=swap">
<style>
:root{
  --pink:#d4558a;
  --pink-soft:#e07aa4;
  --pink-deep:#9b1045;
  --wine:#8a2e55;
  --cell:#7a1638;
  --ink:#000;
  --paper:#fff;
  --muted:#d8d8d8;
  --blue:#3ab4e8;
  --panel:#141414;
}
*{box-sizing:border-box;margin:0;padding:0}
html,body{width:1011px;height:1200px;overflow:hidden}
body{
  position:relative;
  font-family:"Ubuntu",sans-serif;
  color:var(--paper);
  background:
    radial-gradient(ellipse 420px 260px at 120px 1000px,rgba(255,255,255,.28),transparent 70%),
    radial-gradient(ellipse 380px 220px at 880px 160px,rgba(255,255,255,.22),transparent 70%),
    radial-gradient(ellipse 300px 500px at 960px 700px,rgba(255,255,255,.18),transparent 70%),
    radial-gradient(ellipse 360px 200px at 560px 1140px,rgba(255,255,255,.2),transparent 70%),
    linear-gradient(135deg,#3a3a3a 0%,#111 35%,#4a4a4a 55%,#1a1a1a 75%,#3c3c3c 100%);
}
.abs{position:absolute}

/* header */
.phone-top{left:748px;top:38px;font-size:20px;font-weight:300;display:flex;align-items:center;gap:8px;letter-spacing:.5px}
.search{left:750px;top:89px;width:190px;height:27px;background:#f2f2f2;border-radius:3px;border:1px solid #bbb;display:flex}
.search span{flex:1;font-size:9px;color:#777;padding:8px 12px}
.search i{width:29px;background:var(--pink);border-radius:0 3px 3px 0;display:flex;align-items:center;justify-content:center}

/* frame */
.frame{left:76px;top:141px;width:864px;height:927px;border:8px solid var(--pink);border-radius:22px;background:var(--ink)}
.hero-glow{left:303px;top:0;width:413px;height:245px;background:radial-gradient(ellipse at 50% 55%,rgba(212,85,138,.55),rgba(60,10,30,.3) 55%,transparent 75%)}
.brand{left:303px;top:84px;width:413px;text-align:center;font-size:34px;font-weight:500;line-height:38px;color:var(--paper);letter-spacing:1px}
.portrait{left:590px;top:194px;width:341px;height:309px;background:radial-gradient(ellipse 55% 60% at 55% 50%,#e9c487,#b88a4c 55%,#2a1a0c 85%,#000)}
.welcome{left:83px;top:324px;width:328px;height:110px;background:var(--wine);border:1px solid #b25a7f;border-left:none}
.welcome .arrow{position:absolute;left:4px;top:38px;width:29px;height:29px;background:#111;display:flex;align-items:center;justify-content:center}
.welcome h2{position:absolute;right:20px;top:9px;text-align:right;font-weight:400;font-size:20px;line-height:28px}
.welcome h2 b{font-weight:400;font-size:24px}
.welcome .more{position:absolute;left:212px;top:68px;width:104px;height:35px;border-radius:18px;background:linear-gradient(#333,#000);box-shadow:0 1px 0 #c76;font-size:15px;color:var(--pink-soft);display:flex;align-items:center;justify-content:center}

/* nav */
.nav{left:84px;top:505px;width:847px;height:42px;display:flex;background:var(--pink)}
.nav a{color:var(--paper);text-decoration:none;font-size:15px;display:flex;align-items:center;justify-content:center;border-right:1px solid #b63f70}
.nav a.active{background:var(--pink-deep)}

/* content */
.title{left:110px;top:577px;font-size:20px;font-weight:300}
.title em{font-style:normal;color:var(--pink-soft)}
.rule{left:110px;height:1px;width:507px;background:#7a2a4a}
.intro{left:114px;top:624px;width:510px;font-size:12px;line-height:15px;color:var(--muted);text-align:justify}
.intro p+p{margin-top:15px}
.link{font-size:10.5px;color:var(--pink-soft)}
.map{left:114px;top:841px;width:312px;height:166px;border:2px solid #ddd;background:linear-gradient(135deg,#eee6d2,#f3efe4 50%,#e9dcb0)}
.contact-text{left:441px;top:848px;width:180px;font-size:11px;line-height:17.5px;color:var(--muted);text-align:justify}
.c-line{left:441px;display:flex;align-items:center;gap:8px;color:var(--muted)}

/* calendar */
.cal{left:694px;top:582px;width:211px;height:203px;background:var(--pink);border:2px solid var(--pink-soft);border-radius:6px}
.cal-head{height:34px;display:flex;align-items:center;justify-content:space-between;padding:0 8px;background:linear-gradient(#e886ae,var(--pink));border-radius:5px 5px 0 0;font-size:12px;color:#3b0a1e}
.dot{width:14px;height:14px;border-radius:50%;background:#bde4f7;display:flex;align-items:center;justify-content:center}
.cal table{border-collapse:separate;border-spacing:2px;margin:2px auto 0;font-size:11px;text-align:center}
.cal th{font-weight:400;color:#3b0a1e;height:18px;width:26px;font-size:11.5px}
.cal td{background:var(--cell);height:20px;color:var(--paper)}
.cal td.off{color:var(--blue)}
.cal td.today{background:var(--paper);color:var(--pink)}
.cal td.sel{font-weight:500}

/* posts */
.posts{left:693px;top:805px;width:212px;height:227px;background:var(--panel);border:1px solid #555;border-radius:4px}
.posts h3{height:41px;border-bottom:1px solid #444;background:#000;border-radius:4px 4px 0 0;color:var(--pink-soft);font-weight:400;font-size:15px;padding:13px 0 0 20px}
.post{padding:10px 14px 0 21px;position:relative}
.post:before{content:"›";position:absolute;left:9px;top:8px;font-size:14px}
.post h4{font-weight:400;font-size:14px}
.post p{font-size:10px;line-height:17.5px;color:var(--muted);text-align:justify}
.posts .link{position:absolute;right:8px;bottom:14px}

/* footer */
.social{left:82px;top:1103px;display:flex;gap:11px}
.social i{width:22px;height:22px;border-radius:3px;background:#777;border:1px solid #999}
.foot{right:81px;text-align:right;font-size:10.5px;color:var(--paper)}
</style>
</head>
<body>

<div class="abs hero-glow" role="img" aria-label="Ornamental pink flourish behind the salon name"></div>

<div class="abs phone-top">
  <svg width="20" height="20" viewBox="0 0 24 24"><path fill="#d4558a" d="M6.6 10.8a15 15 0 0 0 6.6 6.6l2.2-2.2a1 1 0 0 1 1-.25 11.4 11.4 0 0 0 3.6.57 1 1 0 0 1 1 1V20a1 1 0 0 1-1 1A17 17 0 0 1 3 4a1 1 0 0 1 1-1h3.5a1 1 0 0 1 1 1c0 1.25.2 2.45.57 3.57a1 1 0 0 1-.25 1z"/></svg>
  +1 555 014 2290
</div>
<div class="abs search"><span>Search</span><i><svg width="12" height="12" viewBox="0 0 12 12"><circle cx="5" cy="5" r="3.5" fill="none" stroke="#fff" stroke-width="1.6"/><path d="M7.5 7.5 11 11" stroke="#fff" stroke-width="1.8"/></svg></i></div>

<div class="abs frame"></div>
<div class="abs portrait" role="img" aria-label="Portrait photograph of a smiling woman with long blonde waves"></div>
<div class="abs hero-glow" style="opacity:.6"></div>
<div class="abs brand">VELMORA<br>COIFFURE</div>

<div class="abs welcome">
  <span class="arrow"><svg width="10" height="12" viewBox="0 0 10 12"><path d="M7 1 2 6l5 5" fill="none" stroke="#fff" stroke-width="2"/></svg></span>
  <h2>Welcome to<br>Velmora <b>COIFFURE</b></h2>
  <span class="more">More</span>
</div>

<nav class="abs nav">
  <a class="active" style="width:141px">Home</a>
  <a style="width:140px">About Us</a>
  <a style="width:137px">Services</a>
  <a style="width:131px">Gallery</a>
  <a style="width:119px">Blog</a>
  <a style="width:179px;border:none">Contact Us</a>
</nav>

<h1 class="abs title" style="font-weight:300">Welcome to <em>Velmora Coiffure</em></h1>
<div class="abs rule" style="top:607px"></div>
<div class="abs intro">
  <p>Our salon is based on the belief that our customers needs are of the utmost importance. Our team is committed to meeting those needs. As a result, a high percentage of our business is from repeat customers and referrals.</p>
  <p>We would welcome the opportuniry to earn your trust and deliver you the best service in the industry!</p>
</div>
<div class="abs link" style="left:581px;top:713px">More &gt;&gt;</div>

<h2 class="abs title" style="top:780px;font-weight:300">Contact</h2>
<div class="abs rule" style="top:810px;background:#555"></div>
<div class="abs map" role="img" aria-label="Street map of the salon's neighbourhood"></div>
<p class="abs contact-text">We are located in the very heart of Toronoto, the upscale sophisticated area of Yorkville</p>
<div class="abs c-line" style="top:924px;font-size:13px">
  <svg width="16" height="16" viewBox="0 0 24 24"><path fill="#d4558a" d="M6.6 10.8a15 15 0 0 0 6.6 6.6l2.2-2.2a1 1 0 0 1 1-.25 11.4 11.4 0 0 0 3.6.57 1 1 0 0 1 1 1V20a1 1 0 0 1-1 1A17 17 0 0 1 3 4a1 1 0 0 1 1-1h3.5a1 1 0 0 1 1 1c0 1.25.2 2.45.57 3.57a1 1 0 0 1-.25 1z"/></svg>
  +1 555 014 2290
</div>
<div class="abs c-line" style="top:952px;font-size:11px">
  <svg width="16" height="11" viewBox="0 0 16 11"><rect x=".5" y=".5" width="15" height="10" fill="#d4558a"/><path d="M1 1l7 5 7-5" fill="none" stroke="#fff"/></svg>
  hello@velmoracoiffure.example
</div>

<div class="abs cal">
  <div class="cal-head">
    <span class="dot"><svg width="6" height="8" viewBox="0 0 6 8"><path d="M5 0 0 4l5 4z" fill="#2a8fd0"/></svg></span>
    <span>January 2014</span>
    <span class="dot"><svg width="6" height="8" viewBox="0 0 6 8"><path d="M1 0l5 4-5 4z" fill="#2a8fd0"/></svg></span>
  </div>
  <table>
    <tr><th>Su</th><th>Mo</th><th>Tu</th><th>We</th><th>Th</th><th>Fr</th><th>Sa</th></tr>
    <tr><td class="off">25</td><td class="off">26</td><td class="off">27</td><td class="off">28</td><td class="off">29</td><td class="off">30</td><td>1</td></tr>
    <tr><td>2</td><td>3</td><td>4</td><td>5</td><td>6</td><td>7</td><td class="today">8</td></tr>
    <tr><td>9</td><td>10</td><td>11</td><td>12</td><td>13</td><td class="sel">14</td><td>15</td></tr>
    <tr><td>16</td><td>17</td><td>18</td><td>19</td><td>20</td><td>21</td><td>22</td></tr>
    <tr><td>23</td><td>24</td><td>25</td><td>26</td><td>27</td><td>28</td><td>29</td></tr>
    <tr><td>30</td><td class="off">1</td><td class="off">2</td><td class="off">3</td><td class="off">4</td><td class="off">5</td><td class="off">6</td></tr>
  </table>
</div>

<aside class="abs posts">
  <h3>RECENT POSTS</h3>
  <div class="post"><h4>January 6, 2014</h4><p>by Dr. Lune There is too much hairspray on the shelf if you go to the....</p></div>
  <div class="post"><h4>December 14, 2013</h4><p>“How to Look Expensive ” by Celia Varnhold. A beauty editor's secrets to getting gorfeous...</p></div>
  <span class="link">More &gt;&gt;</span>
</aside>

<div class="abs social" aria-label="Social links">
  <i></i><i></i><i></i><i></i><i></i><i></i>
</div>
<div class="abs foot" style="top:1099px">Privacy &nbsp;&nbsp;|&nbsp;&nbsp; Terms of Use &nbsp;&nbsp;|&nbsp;&nbsp; Contact Us</div>
<div class="abs foot" style="top:1119px">© 2014 velmoracoiffure.example. All rights reserved</div>
<div class="abs foot" style="top:1140px">X2</div>

</body>
</html>
```